Locksmith Business Cards

My father-in-law is in need of new business cards for his locksmith business and I need to impress him. Kindly help me out!

You can see the previous business card attached. It is a family run business in North Wales.

No individual names on the cards.

Key Things to Feature:
- The words "Prompt", "Local", "Reliable" (as you can see under the logo on the website)
- 24h Emergency Service
- Covering All of North Wales, the Wirral and Chester
- The color blue
- A key or a lock would be interesting (similar to the ones that come up when you google locksmith business card)

Optional (only if design includes bullet points, like the example below):
https://imgvaultcdn.net/samples/208314/55172/55172_3904821_208314_image.jpg
- Residential / Commercial / Automotive
- Alarms & Cameras
- Key Cutting & Safes

https://www.brynhafod-locksmiths.co.uk/

Industry/Entity Type

Locksmith

Contact Information for Business Card

01632 960 418
07700 900 362
brynhafodlocksmiths@mailvane.com
Brynhafod Locksmiths, The Willow Barn, 7 Tannery Rd., Llandudno LL99 4QX
www.brynhafod-locksmiths.co.uk

Requirements
Must have
• - The words "Prompt", "Local", "Reliable" (as you can see under the logo on the website)
• - 24h Emergency Service
• - Covering All of North Wales, the Wirral and Chester
Nice to have
• - A key or a lock would be interesting (similar to the ones that come up when you google locksmith business card)

```html
<!DOCTYPE html>
<html lang="en">
<head>
<meta charset="utf-8">
<title>Brynhafod Locksmiths – Business Cards</title>
<link rel="stylesheet" href="https://fonts.googleapis.com/css2?family=Open+Sans:wght@400;600&family=Oswald:wght@500&display=swap">
<style>
  :root {
    --navy: #1f2a63;
    --band-blue: #4d60a6;
    --mid-blue: #3a4d9a;
    --tagline: #b7c0e4;
    --white: #ffffff;
    --ink: #1d2030;
    --page: #e6e6e6;
    --card-radius: 26px;
  }
  * { box-sizing: border-box; margin: 0; padding: 0; }
  html, body { width: 1200px; height: 900px; overflow: hidden; }
  body {
    background: var(--page);
    font-family: "Open Sans", Arial, sans-serif;
    position: relative;
  }
  .card {
    position: absolute;
    width: 640px;
    height: 366px;
    border-radius: var(--card-radius);
    overflow: hidden;
    box-shadow: 0 6px 18px rgba(0,0,0,.18);
  }

  /* ---------- Front ---------- */
  .card-front { left: 60px; top: 60px; background: var(--navy); }
  .card-front .brand {
    position: absolute; left: 210px; top: 58px;
    display: flex; align-items: center; gap: 18px;
  }
  .brand-mark { width: 74px; height: 74px; border-radius: 8px; background: var(--white); flex: none; }
  .brand-name {
    font-family: "Oswald", "Arial Narrow", sans-serif;
    font-weight: 500; font-size: 44px; line-height: 1.0;
    letter-spacing: 1px; text-transform: uppercase;
    color: var(--white);
  }
  .tagline {
    position: absolute; left: 302px; top: 158px;
    font-size: 15px; letter-spacing: 2.5px; font-weight: 600;
    color: var(--tagline);
  }
  .services-band {
    position: absolute; left: 0; right: 0; top: 222px; height: 108px;
    background: var(--band-blue);
    display: flex; flex-direction: column; align-items: center; justify-content: center;
    color: var(--white); font-size: 19px; line-height: 1.4;
  }
  .services-band .dot { display: inline-block; width: 8px; height: 8px; border-radius: 50%; background: var(--white); margin: 0 10px 3px; vertical-align: middle; }

  /* ---------- Back ---------- */
  .card-back { left: 500px; top: 474px; background: var(--white); }
  .card-back .brand {
    position: absolute; right: 40px; top: 44px;
    display: flex; align-items: center; gap: 16px;
  }
  .card-back .brand-mark { background: var(--navy); width: 70px; height: 70px; }
  .card-back .brand-name { color: var(--navy); font-size: 40px; }
  .address {
    position: absolute; right: 40px; top: 140px;
    text-align: right; font-size: 15px; line-height: 1.35; color: var(--ink);
  }
  .contact-list {
    position: absolute; left: 36px; top: 176px;
    list-style: none; font-size: 17px; line-height: 1.45; color: var(--ink);
  }
  .contact-list li { display: flex; align-items: center; gap: 9px; }
  .contact-list svg { width: 15px; height: 15px; fill: var(--navy); flex: none; }
  .emergency-band {
    position: absolute; left: 0; right: 0; bottom: 0; height: 86px;
    background: var(--navy); color: var(--white);
    display: flex; flex-direction: column; align-items: flex-end; justify-content: center;
    padding-right: 40px; text-align: center;
  }
  .emergency-band .inner { text-align: center; }
  .emergency-title { font-weight: 600; font-size: 18px; letter-spacing: .5px; }
  .coverage { font-size: 16px; }
</style>
</head>
<body>

  <section class="card card-front" aria-label="Business card front">
    <div class="brand">
      <span class="brand-mark"></span>
      <div class="brand-name">Brynhafod<br>Locksmiths</div>
    </div>
    <p class="tagline">PROMPT. LOCAL. RELIABLE</p>
    <div class="services-band">
      <p>Residential / Commercial / Automotive</p>
      <p>Alarms &amp; Cameras<span class="dot"></span>Key Cutting &amp; Safes</p>
    </div>
  </section>

  <section class="card card-back" aria-label="Business card back">
    <div class="brand">
      <span class="brand-mark"></span>
      <div class="brand-name">Brynhafod<br>Locksmiths</div>
    </div>
    <address class="address" style="font-style:normal">
      Brynhafod Locksmiths<br>
      The Willow Barn<br>
      7 Tannery Rd., Llandudno<br>
      LL99 4QX
    </address>

    <ul class="contact-list">
      <li>
        <svg viewBox="0 0 16 16" aria-hidden="true"><path d="M3 1h3l1.5 4-2 1.2a9 9 0 0 0 4.3 4.3L11 8.5l4 1.5v3a2 2 0 0 1-2 2C6.9 15 1 9.1 1 3a2 2 0 0 1 2-2z"/></svg>
        01632 960 418
      </li>
      <li>
        <svg viewBox="0 0 16 16" aria-hidden="true"><path d="M4 0h8a1 1 0 0 1 1 1v14a1 1 0 0 1-1 1H4a1 1 0 0 1-1-1V1a1 1 0 0 1 1-1zm1 2v10h6V2zm3 11a1 1 0 1 0 0 2 1 1 0 0 0 0-2z"/></svg>
        07700 900 362
      </li>
      <li>
        <svg viewBox="0 0 16 16" aria-hidden="true"><path d="M0 3h16v10H0zm1.5 1.2L8 9l6.5-4.8V4h-13z"/></svg>
        brynhafodlocksmiths@mailvane.com
      </li>
      <li>
        <svg viewBox="0 0 16 16" aria-hidden="true"><path d="M8 0a8 8 0 1 1 0 16A8 8 0 0 1 8 0zm0 1.5c-1 1.3-1.6 3-1.7 5.5h3.4C9.6 4.5 9 2.8 8 1.5zM1.6 7h3.2c.1-2 .6-3.7 1.4-5A6.5 6.5 0 0 0 1.6 7zm9.6 0h3.2a6.5 6.5 0 0 0-4.6-5c.8 1.3 1.3 3 1.4 5zM1.6 9a6.5 6.5 0 0 0 4.6 5c-.8-1.3-1.3-3-1.4-5zm4.7 0c.1 2.5.7 4.2 1.7 5.5 1-1.3 1.6-3 1.7-5.5zm4.9 0c-.1 2-.6 3.7-1.4 5a6.5 6.5 0 0 0 4.6-5z"/></svg>
        www.brynhafod-locksmiths.co.uk
      </li>
    </ul>

    <div class="emergency-band">
      <div class="inner">
        <p class="emergency-title">24H EMERGENCY SERVICE</p>
        <p class="coverage">Covering All of North Wales, the Wirral and Chester</p>
      </div>
    </div>
  </section>

</body>
</html>
```